Brindle Asset Management Vendor Recruiting Email

We need a digital flyer to email and post on Social media to attract new vendors to our website to apply to complete maintenance work on our clients homes. I have one flyer we had produced recently that we are un-happy with. It is attached.

The example given is what we do not want!! We do not want any of the pictures used from the existing one

Target Market(s)

Construction companies and handyman

Industry/Entity Type

Residential maintenance and repairs

Requirements
Must have
• Join our team as the header not become a vendor

```html
<!DOCTYPE html>
<html lang="en">
<head>
<meta charset="utf-8">
<title>Brindle Asset Management – Join Our Team</title>
<link href="https://fonts.googleapis.com/css2?family=Archivo:wdth,wght@125,800;125,900&family=Inter:wght@400;500&display=swap" rel="stylesheet">
<style>
  :root {
    --page: #ffffff;
    --navy: #03021a;
    --cyan: #00e5f5;
    --sky: #0a9bf5;
    --deep-blue: #0a3a9a;
    --magenta: #ff12e6;
    --white: #ffffff;
    --band-yellow: #fcc72c;
    --band-orange: #fb9703;
    --band-sand: #fdc95e;
    --tagline: #fcb410;
    --req-blue: #1a9fff;
    --box-top: #0b6fd6;
    --box-bottom: #0a9bff;
    --marker: #5a5a66;
    --heading: "Archivo", "Arial Black", sans-serif;
    --body: "Inter", Arial, sans-serif;
  }
  * { margin: 0; padding: 0; box-sizing: border-box; }
  html, body { width: 1200px; height: 2337px; overflow: hidden; background: var(--page); }
  .board { position: relative; width: 1200px; height: 2337px; }

  .flyer {
    position: absolute; left: 312px; width: 577px;
    background: var(--navy); overflow: hidden;
    box-shadow: 0 24px 50px rgba(0,0,0,.28);
    color: var(--white);
  }
  .flyer > * { position: absolute; }
  .flyer--square { top: 223px; height: 720px; }
  .flyer--tall { top: 1139px; height: 1024px; }

  .photo { left: 0; top: 0; width: 100%;
    background: linear-gradient(180deg, var(--cyan) 0%, var(--sky) 30%, var(--deep-blue) 65%, var(--navy) 100%); }

  .brand { left: 0; width: 100%; text-align: center; font-family: var(--body); font-weight: 500; color: var(--white); letter-spacing: .04em; }
  .brand__mark { display: block; margin: 0 auto 8px; background: var(--white); }

  .headline { left: 0; width: 100%; text-align: center; font-family: var(--heading); font-weight: 900; font-stretch: 125%; line-height: 1; letter-spacing: -.02em; }
  .headline--pink { color: var(--magenta); }
  .headline--white { color: var(--white); }

  .bands { left: 0; width: 100%; display: flex; gap: 3px; }
  .band { flex: 1; display: flex; align-items: center; justify-content: center; text-align: center;
    font-family: var(--heading); font-weight: 900; font-stretch: 125%; line-height: 1; color: var(--navy); }
  .band--yellow { background: var(--band-yellow); }
  .band--orange { background: var(--band-orange); }
  .band--sand { background: var(--band-sand); }

  .benefits { list-style: none; font-family: var(--body); line-height: 1.2; display: flex; flex-direction: column; justify-content: space-between; }
  .benefits li { position: relative; }
  .benefits li::before { content: ""; position: absolute; left: -17px; top: 2px; bottom: 2px; width: 6px; background: var(--marker); }

  .req-label { writing-mode: vertical-rl; transform: rotate(180deg); font-family: var(--heading); font-weight: 900; font-stretch: 125%; color: var(--req-blue); text-align: left; line-height: 1; }

  .requirements { list-style: none; background: linear-gradient(180deg, var(--box-top), var(--box-bottom)); font-family: var(--body); line-height: 1.2; display: flex; flex-direction: column; justify-content: space-between; }
  .requirements li { border-bottom: 1px solid rgba(255,255,255,.45); }
  .requirements li:last-child { border-bottom: none; }

  .tagline { left: 0; width: 100%; text-align: center; font-family: var(--heading); font-weight: 800; font-stretch: 125%; color: var(--tagline); line-height: 1.3; }
  .website { left: 0; width: 100%; text-align: center; font-family: var(--body); font-weight: 500; color: var(--white); letter-spacing: .02em; }
  .website span { color: var(--cyan); }
  .callbar { left: 0; width: 100%; bottom: 0; background: var(--sky); display: flex; align-items: center; justify-content: center; gap: 6px;
    font-family: var(--heading); font-weight: 900; font-stretch: 125%; color: var(--white); letter-spacing: .03em; }

  /* square flyer */
  .flyer--square .photo { height: 200px; }
  .flyer--square .brand { top: 110px; font-size: 13px; }
  .flyer--square .brand__mark { width: 14px; height: 14px; }
  .flyer--square .headline--pink { top: 186px; font-size: 50px; }
  .flyer--square .headline--white { top: 238px; font-size: 50px; }
  .flyer--square .bands { top: 290px; height: 47px; }
  .flyer--square .band { font-size: 15px; }
  .flyer--square .benefits { left: 79px; top: 363px; width: 200px; height: 262px; font-size: 14.5px; }
  .flyer--square .req-label { left: 311px; top: 352px; height: 276px; font-size: 23px; }
  .flyer--square .requirements { left: 341px; top: 352px; width: 185px; height: 276px; padding: 18px 14px 14px; font-size: 13px; }
  .flyer--square .requirements li { padding-bottom: 5px; }
  .flyer--square .tagline { top: 638px; font-size: 17px; }
  .flyer--square .website { top: 664px; font-size: 17px; }
  .flyer--square .callbar { height: 35px; font-size: 18px; }

  /* tall flyer */
  .flyer--tall .photo { height: 250px; }
  .flyer--tall .brand { top: 168px; font-size: 17px; }
  .flyer--tall .brand__mark { width: 18px; height: 18px; }
  .flyer--tall .headline--pink { top: 250px; font-size: 74px; }
  .flyer--tall .headline--white { top: 322px; font-size: 70px; }
  .flyer--tall .bands { top: 399px; height: 71px; }
  .flyer--tall .band { font-size: 20px; }
  .flyer--tall .benefits { left: 44px; top: 500px; width: 250px; height: 335px; font-size: 20px; }
  .flyer--tall .benefits li::before { left: -20px; width: 7px; }
  .flyer--tall .req-label { left: 292px; top: 492px; height: 348px; font-size: 31px; }
  .flyer--tall .requirements { left: 329px; top: 492px; width: 233px; height: 348px; padding: 22px 18px 18px; font-size: 17.5px; }
  .flyer--tall .requirements li { padding-bottom: 6px; }
  .flyer--tall .tagline { top: 857px; font-size: 25px; }
  .flyer--tall .website { top: 945px; font-size: 23px; }
  .flyer--tall .callbar { height: 46px; font-size: 23px; }
</style>
</head>
<body>
<main class="board">

  <section class="flyer flyer--square">
    <div class="photo" role="img" aria-label="Blue-toned photo of a handshake and a contractor in a hard hat working on pipes"></div>
    <div class="brand"><span class="brand__mark"></span>Brindle Asset Management</div>
    <h1 class="headline headline--pink">JOIN OUR</h1>
    <div class="headline headline--white">TEAM</div>
    <div class="bands">
      <div class="band band--yellow">EASY<br>APPLICATION</div>
      <div class="band band--orange">QUICK<br>PAYMENT</div>
      <div class="band band--sand">LOCAL &amp;<br>SIMPLE</div>
    </div>
    <ul class="benefits">
      <li>95% approval rating on all submitted estimates.</li>
      <li>Guaranteed work volume.</li>
      <li>Material purchasing program to help vendors</li>
      <li>With low capital or no or bad credit.</li>
      <li>Weekly secure direct deposit with</li>
      <li>Net 30 payment terms.</li>
    </ul>
    <div class="req-label">REQUIREMENTS</div>
    <ul class="requirements">
      <li>Auto insurance</li>
      <li>Certificate of general liability insurance</li>
      <li>Workman's compensation or state issued exemption letter</li>
      <li>Drive license or state issued ID card</li>
      <li>Coverage area</li>
      <li>Any specialty licenses</li>
    </ul>
    <p class="tagline">Join our team Now...! Fill out you application..!</p>
    <p class="website"><span>WWW.</span>BRINDLEASSETMANAGEMENT<span>.COM</span></p>
    <div class="callbar">
      <svg width="15" height="15" viewBox="0 0 16 16" aria-hidden="true"><rect x="1" y="1" width="14" height="14" rx="4" fill="#fff"/><path d="M5 4.5c0 3.8 2.7 6.8 6.5 7l.6-1.8-2-1-.9.9c-1-.5-1.8-1.3-2.3-2.3l.9-.9-1-2z" fill="#0a9bf5"/></svg>
      555-014-2290
    </div>
  </section>

  <section class="flyer flyer--tall">
    <div class="photo" role="img" aria-label="Blue-toned photo of a handshake and a contractor in a hard hat working on pipes"></div>
    <div class="brand"><span class="brand__mark"></span>Brindle Asset Management</div>
    <h2 class="headline headline--pink">JOIN OUR</h2>
    <div class="headline headline--white">TEAM</div>
    <div class="bands">
      <div class="band band--yellow">EASY<br>APPLICATION</div>
      <div class="band band--orange">QUICK<br>PAYMENT</div>
      <div class="band band--sand">LOCAL &amp;<br>SIMPLE</div>
    </div>
    <ul class="benefits">
      <li>95% approval rating on all submitted estimates.</li>
      <li>Guaranteed work volume.</li>
      <li>Material purchasing program to help vendors</li>
      <li>With low capital or no or bad credit.</li>
      <li>Weekly secure direct deposit with</li>
      <li>Net 30 payment terms.</li>
    </ul>
    <div class="req-label">REQUIREMENTS</div>
    <ul class="requirements">
      <li>Auto insurance</li>
      <li>Certificate of general liability insurance</li>
      <li>Workman's compensation or state issued exemption letter</li>
      <li>Drive license or state issued ID card</li>
      <li>Coverage area</li>
      <li>Any specialty licenses</li>
    </ul>
    <p class="tagline">Join our team Now...!<br>Fill out you application..!</p>
    <p class="website"><span>WWW.</span>BRINDLEASSETMANAGEMENT<span>.COM</span></p>
    <div class="callbar">
      <svg width="19" height="19" viewBox="0 0 16 16" aria-hidden="true"><rect x="1" y="1" width="14" height="14" rx="4" fill="#fff"/><path d="M5 4.5c0 3.8 2.7 6.8 6.5 7l.6-1.8-2-1-.9.9c-1-.5-1.8-1.3-2.3-2.3l.9-.9-1-2z" fill="#0a9bf5"/></svg>
      555-014-2290
    </div>
  </section>

</main>
</body>
</html>
```